Landing Page and Logo for Auto-Blogging Platform

I created a platform that allows users to start a blog for their business, hobby, charity, etc. I need a landing page where users can learn about the platform, benefits of consistent blogging, SEO value, plans/pricing, etc. The landing page needs to have multiple call to action buttons encouraging the visitor to register/sign up for a free trial.

In addition to the landing page, I need a page for users to establish the settings for their blog. This page should be a fairly simple form, intended for the user to enter a few details to set up their blog:
1. Name of Blog
2. Up to 10 topics and/or keywords the blog should focus on
3. Theme: Color-scheme and logo upload for blog.

I have attached the specifications of the platform's functionality so you can better understand how it works, plans/pricing, etc.

I also need a logo for the business. The name of the platform is PostNook.

Target Market(s)

Website owners, bloggers, business owners

Industry/Entity Type

Technology, Internet, web design

Coding

Coded - Design and coding required

Number of Pages Required

2 page

Colors
0054AA
0677BA
7BADD7
CADEEF
E8F1F8
0094D4
00A9DD
6FCCEA
C7EBF8
E9F6FB

Requirements
Must have
• Eye-catching design but fairly light on content (keep it simple and brief.)
Nice to have
• Eye-catching yet simple design, clean and easy to understand what we are offering.
Should not have
• Too much “wordy” and confusing content.

```html
<!DOCTYPE html>
<html lang="en">
<head>
<meta charset="utf-8">
<title>PostNook – Transform Your Online Presence</title>
<link href="https://fonts.googleapis.com/css2?family=Poppins:wght@400;500;600;700;800&display=swap" rel="stylesheet">
<style>
:root{
  --blue-900:#0054AA;
  --blue-700:#0677BA;
  --blue-500:#0094D4;
  --blue-400:#00A9DD;
  --blue-300:#6FCCEA;
  --blue-200:#7BADD7;
  --blue-150:#C7EBF8;
  --blue-100:#CADEEF;
  --blue-50:#E8F1F8;
  --ink:#1d1d1f;
  --muted:#6b6b70;
  --dark:#2a2a2c;
  --white:#ffffff;
  --star:#f4a21b;
  --grad:linear-gradient(90deg,var(--blue-900),var(--blue-300));
  --grad-diag:linear-gradient(135deg,var(--blue-900) 0%,var(--blue-700) 40%,var(--blue-300) 100%);
}
*{box-sizing:border-box;margin:0;padding:0}
html,body{width:1200px;height:3444px;overflow:hidden;background:var(--white)}
body{font-family:'Poppins',sans-serif;color:var(--ink);position:relative}
.abs{position:absolute}
a{color:inherit;text-decoration:none}

/* nav */
.brand{font-weight:700;color:var(--blue-700);font-size:26px;letter-spacing:-.3px}
.nav{left:0;top:0;width:1200px;height:70px}
.nav .brand{left:89px;top:15px}
.nav-links{left:481px;top:24px;display:flex;gap:19px;font-size:13px;color:#444}
.nav-links .active{color:var(--blue-900);font-weight:600;position:relative}
.nav-links .active::after{content:"";position:absolute;left:50%;top:24px;width:7px;height:7px;margin-left:-3.5px;border-radius:50%;background:var(--blue-900)}
.login{left:887px;top:24px;font-size:13px;font-weight:600;display:flex;gap:8px;align-items:center}
.btn-register{left:958px;top:14px;width:152px;height:42px;border-radius:21px;background:var(--grad);color:#fff;font-size:14px;font-weight:600;display:flex;align-items:center;justify-content:center}

/* buttons */
.pill{display:flex;align-items:center;justify-content:space-between;border-radius:24px;background:var(--grad);color:#fff;font-weight:600;font-size:14px;padding:0 5px 0 20px;box-shadow:0 4px 10px rgba(0,84,170,.18)}
.pill .arrow{width:32px;height:32px;border-radius:50%;background:var(--blue-900);border:2px solid #fff;display:flex;align-items:center;justify-content:center}
.pill.light{background:#fff;color:var(--ink)}
.pill.light .arrow{border-color:var(--blue-900)}

/* hero */
.hero-art{left:585px;top:105px;width:540px;height:540px;border-radius:40px;background:radial-gradient(circle at 45% 45%,var(--blue-300),var(--blue-150) 50%,rgba(233,246,251,0) 70%);z-index:0}
.hero-title{left:90px;top:204px;font-size:45px;line-height:55px;font-weight:800;letter-spacing:-.3px;white-space:nowrap;z-index:2}
.hero-title .grad{background:var(--grad);-webkit-background-clip:text;background-clip:text;color:transparent}
.hero-sub{left:90px;top:387px;font-size:12px;color:#444;z-index:2}
.hero-cta{left:90px;top:425px;width:215px;height:43px;z-index:2}
.rating{left:90px;top:508px;width:222px;height:82px;border-radius:14px;background:#fff;box-shadow:0 8px 30px rgba(0,0,0,.08);display:flex;align-items:center;gap:12px;padding-left:26px;z-index:2}
.rating .score{font-size:44px;font-weight:700}
.rating .stars{color:var(--star);font-size:13px;letter-spacing:2px}
.rating .meta{font-size:11px;color:#444;line-height:15px}

/* section heads */
.eyebrow{width:1200px;left:0;text-align:center;font-size:13px;font-weight:600;color:var(--blue-900)}
.h2{width:1200px;left:0;text-align:center;font-size:37px;font-weight:600;letter-spacing:-.3px}

/* steps */
.step{width:244px;height:216px;top:840px;border-radius:18px;background:#fff;box-shadow:0 6px 26px rgba(0,0,0,.08);text-align:center;padding-top:20px}
.step .ico{width:58px;height:58px;margin:0 auto 8px;border-radius:14px;background:linear-gradient(135deg,var(--blue-300),var(--blue-900))}
.step .ico.round{border-radius:50%}
.step h3{font-size:18px;font-weight:600;margin-bottom:8px}
.step p{font-size:11.5px;line-height:19px;color:#666;padding:0 26px}
.step .go{position:absolute;left:50%;bottom:-22px;margin-left:-21px;width:42px;height:42px;border-radius:50%;background:var(--grad-diag);border:3px solid #fff;display:flex;align-items:center;justify-content:center;box-shadow:0 4px 10px rgba(0,84,170,.25)}

/* why */
.why-art{left:110px;top:1215px;width:480px;height:455px;border-radius:30px;background:radial-gradient(circle at 50% 50%,var(--blue-100),var(--blue-50) 55%,rgba(255,255,255,0) 75%)}
.why-title{left:643px;top:1256px;font-size:37px;line-height:44px;font-weight:600;letter-spacing:-.3px}
.why-text{left:643px;top:1364px;width:440px;font-size:12px;line-height:22.5px;color:#555}
.why-list{left:643px;top:1466px;list-style:none;font-size:12px;color:#444}
.why-list li{height:26.6px;display:flex;align-items:center;gap:9px}
.why-list li::before{content:"";width:9px;height:9px;border-radius:50%;background:var(--blue-900)}
.why-cta{left:643px;top:1588px;width:292px;height:43px}

/* pricing */
.plan{top:1886px;width:272px;height:474px;background:#fff;box-shadow:0 6px 30px rgba(0,0,0,.07);text-align:center}
.plan::after{content:"";position:absolute;left:40px;right:40px;bottom:-26px;height:18px;border-radius:50%;background:radial-gradient(ellipse,rgba(0,0,0,.25),rgba(0,0,0,0) 70%)}
.plan.premium{background:linear-gradient(150deg,var(--blue-900) 0%,var(--blue-700) 35%,var(--blue-300) 100%);color:#fff;border-radius:4px}
.plan h3{font-size:22px;font-weight:600;margin-top:46px}
.plan .posts{font-size:14px;color:#555;margin-top:26px}
.plan .rule{width:180px;height:1px;background:#bbb;margin:18px auto 0}
.plan .words{font-size:23px;margin-top:24px}
.plan .freq{font-size:14px;font-weight:500;margin-top:28px;line-height:20px;height:40px;display:flex;align-items:center;justify-content:center}
.plan .price{font-size:25px;font-weight:600;margin-top:30px}
.plan .get{width:144px;height:45px;border-radius:23px;margin:42px auto 0;background:var(--grad);color:#fff;font-size:14px;font-weight:500;display:flex;align-items:center;justify-content:center}
.plan.premium .posts,.plan.premium .freq{color:#fff}
.plan.premium .rule{background:rgba(255,255,255,.5)}
.plan.premium .get{background:#fff;color:var(--ink)}

/* testimonials */
.arrows{left:993px;top:2475px;display:flex;gap:10px}
.arrows span{width:45px;height:45px;border-radius:50%;border:2px solid #333;display:flex;align-items:center;justify-content:center}
.quote{top:2563px;width:484px;height:254px;border-radius:22px;background:#fff;box-shadow:0 6px 30px rgba(0,0,0,.08)}
.quote .stars{position:absolute;left:35px;top:44px;color:var(--star);font-size:16px;letter-spacing:1px}
.quote p{position:absolute;left:35px;top:75px;width:240px;font-size:11.5px;line-height:16px;color:#555}
.quote .rule{position:absolute;left:35px;top:157px;width:163px;height:1px;background:#ccc}
.quote .who{position:absolute;left:35px;top:177px;font-size:13px;font-weight:600;color:#555}
.quote .avatar{position:absolute;left:283px;top:57px;width:165px;height:165px;border-radius:50%;border:4px solid var(--blue-700);background:linear-gradient(160deg,var(--blue-150),var(--blue-200))}
.quote .mark{position:absolute;left:388px;top:40px;width:58px;height:58px;border-radius:50%;background:var(--grad-diag);border:4px solid #fff;display:flex;align-items:center;justify-content:center;color:#fff;font-size:38px;font-weight:700;line-height:1;padding-top:14px}

/* cta + footer */
.footer{left:0;top:3113px;width:1200px;height:331px;background:var(--dark)}
.cta-band{left:199px;top:2995px;width:801px;height:229px;border-radius:115px;background:linear-gradient(90deg,var(--blue-900),var(--blue-700) 40%,var(--blue-300));text-align:center;color:#fff}
.cta-band h2{font-size:37px;font-weight:600;margin-top:49px}
.cta-band p{font-size:11.5px;margin-top:4px}
.cta-band .pill{margin:22px auto 0;width:225px;height:42px}
.footer .brand{position:absolute;left:89px;top:170px;color:#fff;font-size:46px;font-weight:600}
.foot-links{position:absolute;left:435px;top:190px;display:flex;gap:50px;color:#fff;font-size:14px;font-weight:500}
.foot-rule{position:absolute;left:89px;top:263px;width:1020px;height:1px;background:#666}
.copy{position:absolute;left:0;width:1200px;top:286px;text-align:center;color:#fff;font-size:14px;font-weight:500}
.to-top{position:absolute;left:1122px;top:210px;width:52px;height:52px;border-radius:50%;background:var(--grad-diag);display:flex;align-items:center;justify-content:center}
</style>
</head>
<body>

<header class="nav abs">
  <a class="brand abs">PostNook</a>
  <nav class="nav-links abs">
    <a class="active">Home</a><a>About</a><a>Plan &amp; Pricing</a><a>Testimonial</a><a>Contact</a>
  </nav>
  <a class="login abs"><svg width="12" height="13" viewBox="0 0 12 13"><circle cx="6" cy="3.5" r="3" fill="#0054AA"/><path d="M0 13c0-4 2.6-5.5 6-5.5S12 9 12 13z" fill="#0054AA"/></svg>Login</a>
  <a class="btn-register abs">Register Now</a>
</header>

<section class="hero">
  <div class="hero-art abs" role="img" aria-label="Photos of a smiling woman with a phone and a man with a laptop, surrounded by floating social icons and an award badge"></div>
  <h1 class="hero-title abs"><span class="grad">Transform Your</span><br>Online Presence with<br>PostNook</h1>
  <p class="hero-sub abs">Effortlessly Create, Manage, and Grow Your Blog</p>
  <a class="pill hero-cta abs">Start Your Free Trial<span class="arrow"><svg width="12" height="12" viewBox="0 0 12 12"><path d="M2 10 10 2M4 2h6v6" stroke="#fff" stroke-width="1.5" fill="none"/></svg></span></a>
  <div class="rating abs">
    <span class="score">4.7</span>
    <div><div class="stars">★★★★★</div><div class="meta">1,938 Rating<br>Reviewly Review</div></div>
  </div>
</section>

<section class="steps">
  <p class="eyebrow abs" style="top:730px">How It Works</p>
  <h2 class="h2 abs" style="top:756px">Get Started in 3 Easy Steps</h2>
  <article class="step abs" style="left:206px"><div class="ico" role="img" aria-label="Blog page icon"></div><h3>Create Your Blog</h3><p>Sign up and choose your blog’s name, topics, and keywords.</p><span class="go"><svg width="12" height="12" viewBox="0 0 12 12"><path d="M2 10 10 2M4 2h6v6" stroke="#fff" stroke-width="1.5" fill="none"/></svg></span></article>
  <article class="step abs" style="left:478px"><div class="ico round" role="img" aria-label="Design tools icon"></div><h3>Customize Your Design</h3><p>Pick a theme, upload your logo, and personalize your color scheme.</p><span class="go"><svg width="12" height="12" viewBox="0 0 12 12"><path d="M2 10 10 2M4 2h6v6" stroke="#fff" stroke-width="1.5" fill="none"/></svg></span></article>
  <article class="step abs" style="left:749px"><div class="ico" role="img" aria-label="Publishing megaphone icon"></div><h3>Start Blogging</h3><p>Publish your first post and watch your online presence grow!</p><span class="go"><svg width="12" height="12" viewBox="0 0 12 12"><path d="M2 10 10 2M4 2h6v6" stroke="#fff" stroke-width="1.5" fill="none"/></svg></span></article>
  <a class="pill abs" style="left:487px;top:1114px;width:225px;height:42px">Start Blogging Today<span class="arrow"><svg width="12" height="12" viewBox="0 0 12 12"><path d="M2 10 10 2M4 2h6v6" stroke="#fff" stroke-width="1.5" fill="none"/></svg></span></a>
</section>

<section class="why">
  <div class="why-art abs" role="img" aria-label="Illustration of two people beside a tablet showing blog growth charts"></div>
  <h2 class="why-title abs">Why Blogging Matters<br>for Your Business</h2>
  <p class="why-text abs">Blogging is more than just sharing ideas—it’s a powerful tool to boost your online visibility, establish authority in your niche, and connect with your audience. Consistent blogging drives organic traffic, enhances SEO, and converts visitors into loyal customers.</p>
  <ul class="why-list abs">
    <li>Boosts Search Engine Rankings.</li>
    <li>Builds Authority &amp; Trust.</li>
    <li>Engages &amp; Grows Your Audience.</li>
    <li>Drives Leads &amp; Sales.</li>
  </ul>
  <a class="pill why-cta abs">Learn More About Our Platform<span class="arrow"><svg width="12" height="12" viewBox="0 0 12 12"><path d="M2 10 10 2M4 2h6v6" stroke="#fff" stroke-width="1.5" fill="none"/></svg></span></a>
</section>

<section class="pricing">
  <p class="eyebrow abs" style="top:1771px">Plans &amp; Pricing</p>
  <h2 class="h2 abs" style="top:1797px">Choose the Perfect Plan for Your Needs</h2>
  <article class="plan abs" style="left:177px"><h3>Base Plan</h3><p class="posts">1 blog post</p><div class="rule"></div><p class="words">(up to 2,000 words)</p><div class="rule"></div><p class="freq">every month</p><p class="price">$9.99/mo.</p><a class="get">Get Started</a></article>
  <article class="plan premium abs" style="left:464px"><h3>Premium Plan</h3><p class="posts">1 blog post</p><div class="rule"></div><p class="words">(up to 3,000 words)</p><div class="rule"></div><p class="freq">per day plus unlimited<br>manual posting</p><p class="price">$24.99/mo.</p><a class="get">Get Started</a></article>
  <article class="plan abs" style="left:755px"><h3>Ultimate Plan</h3><p class="posts">1 blog post</p><div class="rule"></div><p class="words">(up to 2,000 words)</p><div class="rule"></div><p class="freq">every month</p><p class="price">$14.99/mo.</p><a class="get">Get Started</a></article>
</section>

<section class="testimonials">
  <p class="eyebrow abs" style="top:2461px">Testimonials</p>
  <h2 class="h2 abs" style="top:2487px">What Our Users Say</h2>
  <div class="arrows abs">
    <span><svg width="12" height="14" viewBox="0 0 12 14"><path d="M9 1 3 7l6 6" stroke="#333" stroke-width="2" fill="none"/></svg></span>
    <span><svg width="12" height="14" viewBox="0 0 12 14"><path d="M3 1l6 6-6 6" stroke="#333" stroke-width="2" fill="none"/></svg></span>
  </div>
  <article class="quote abs" style="left:106px">
    <div class="stars">★★★★★</div>
    <p>Lorem Ipsum is simply dummy text of the printing and typesetting industry. Lorem Ipsum has been the industry’s standard.</p>
    <div class="rule"></div><span class="who">User A</span>
    <div class="avatar" role="img" aria-label="Portrait photo of User A"></div>
    <span class="mark">”</span>
  </article>
  <article class="quote abs" style="left:610px">
    <div class="stars">★★★★★</div>
    <p>Lorem Ipsum is simply dummy text of the printing and typesetting industry. Lorem Ipsum has been the industry’s standard.</p>
    <div class="rule"></div><span class="who">User B</span>
    <div class="avatar" role="img" aria-label="Portrait photo of User B"></div>
    <span class="mark">”</span>
  </article>
  <a class="pill abs" style="left:487px;top:2861px;width:225px;height:42px">Join Our Community<span class="arrow"><svg width="12" height="12" viewBox="0 0 12 12"><path d="M2 10 10 2M4 2h6v6" stroke="#fff" stroke-width="1.5" fill="none"/></svg></span></a>
</section>

<footer class="footer abs">
  <span class="brand">PostNook</span>
  <nav class="foot-links"><a>Home</a><a>About</a><a>Plan &amp; Pricing</a><a>Testimonial</a><a>Contact</a><a>Login/Register</a></nav>
  <div class="foot-rule"></div>
  <p class="copy">© 2024 PostNook. All rights reserved.</p>
  <a class="to-top"><svg width="16" height="18" viewBox="0 0 16 18"><path d="M8 17V2M2 8l6-6 6 6" stroke="#fff" stroke-width="1.6" fill="none"/></svg></a>
</footer>

<section class="cta-band abs">
  <h2>Ready to Transform Your Blog?</h2>
  <p>Sign up today and start your free trial. No credit card required!</p>
  <a class="pill light">Start Your Free Trial<span class="arrow"><svg width="12" height="12" viewBox="0 0 12 12"><path d="M2 10 10 2M4 2h6v6" stroke="#fff" stroke-width="1.5" fill="none"/></svg></span></a>
</section>

</body>
</html>
```